Popup Nightclub Grand Opening Flyer

We need to design a flyer for the grand opening of an upscale, exclusive nightclub called "Lantern". The design needs to be chic and exclusive. The background should be black and the text should primarily be white. We like minimalist designs.

Here is the text for the flyer
-
Velvetroll Atlanta Presents

Lantern (LOGO)

A Popup Nightclub Experience
For one night Only

Friday, October 18, 2013
Party begins at 9PM

INVITE ONLY

See invitation for location details
(Velvetroll Atlanta logo)

-
Examples we like

http://cdn4-x.pressfolio-example.com/sites/default/files/styles/image_content_width/hash/3b/fd/2468013579_4421_flyer.jpg?itok=K9rtQw2z

http://files.hubspace-example.net/files/8Hqq-Tr72WWE3kaRbTmcxP5QZK2F396J8nbRw4CKMHfdX2Y7qSEF-MqjxDoNrLY3QCyQJD7npjGaRq3k-Mhx6hqf3MDSWf8r3/2zenSaturdays.jpg

http://morvex-example.com/wp-content/uploads/siteskin/widgetkit/gallery/2zen/2zen-gen_qstay4-01.jpg

Hi All, one thing that we are seeing that we don't like is on over emphasis on the phrase "a popup nightclub experience" please don't make this the largest thing on the flyer

Target Market(s)

Target market is 25-35 year olds who are affluent (rich) and like luxury brands

Requirements
Must have
• Dark Background
Nice to have
• Velvetroll Logo on the bottom
Modern text that isn't curvy
Should not have
• Curved text

```html
<!DOCTYPE html>
<html lang="en">
<head>
<meta charset="utf-8">
<title>Lantern Nightclub – Popup Flyer</title>
<link rel="stylesheet" href="https://fonts.googleapis.com/css2?family=Barlow:wght@300;400;600&family=Barlow+Condensed:wght@400;600&display=swap">
<style>
  :root {
    --black: #000000;
    --white: #ffffff;
    --silver-light: #f2f2f2;
    --silver-mid: #b9b9b9;
    --silver-dark: #8a8a8a;
    --muted: #a6a6a6;
    --rule: #5a5a5a;
    --band-glow: #3b3b3d;
  }
  html, body {
    margin: 0;
    padding: 0;
    width: 890px;
    height: 1200px;
    overflow: hidden;
    background: var(--black);
  }
  .flyer {
    position: relative;
    width: 890px;
    height: 1200px;
    background: var(--black);
    font-family: "Barlow", sans-serif;
    color: var(--white);
  }
  .row {
    position: absolute;
    left: 0;
    right: 0;
    margin: 0;
    text-align: center;
    transform: translateY(-50%);
    white-space: nowrap;
  }
  .rule {
    position: absolute;
    left: 139px;
    width: 612px;
    height: 3px;
    background: linear-gradient(90deg, transparent, var(--rule) 25%, #6b6b6b 50%, var(--rule) 75%, transparent);
  }
  .rule--top-a { top: 120px; }
  .rule--top-b { top: 181px; }
  .rule--mid-a { top: 475px; }
  .rule--mid-b { top: 765px; }
  .rule--bot-a { top: 965px; }
  .rule--bot-b { top: 1088px; }

  .band {
    position: absolute;
    left: 139px;
    width: 612px;
    background: radial-gradient(ellipse 50% 90% at 50% 50%, var(--band-glow), rgba(30,30,32,0.6) 60%, transparent 100%);
  }
  .band--top { top: 123px; height: 58px; }
  .band--middle {
    top: 478px; height: 287px;
    background: radial-gradient(ellipse 48% 75% at 50% 50%, #4a4a4d, #232325 55%, transparent 100%);
  }
  .band--bottom { top: 968px; height: 120px; }

  .presenter {
    top: 152px;
    font-size: 18px;
    font-weight: 400;
    letter-spacing: 0.2px;
    color: var(--silver-light);
  }
  .presenter strong { font-weight: 600; }

  .venue-mark {
    position: absolute;
    left: 50%;
    top: 214px;
    width: 100px;
    height: 100px;
    margin-left: -50px;
    border-radius: 50%;
    background: linear-gradient(160deg, #f0f0f0, #9a9a9a 55%, #d8d8d8);
  }
  .venue-name {
    top: 380px;
    font-size: 64px;
    font-weight: 300;
    letter-spacing: 12px;
    padding-left: 12px;
    color: var(--white);
  }
  .venue-type {
    top: 431px;
    font-size: 22px;
    font-weight: 300;
    letter-spacing: 6px;
    padding-left: 6px;
    color: var(--white);
  }

  .headline {
    position: absolute;
    left: 0;
    right: 0;
    top: 508px;
    margin: 0;
    text-align: center;
    font-family: "Barlow Condensed", sans-serif;
    font-weight: 600;
    font-size: 50px;
    line-height: 56px;
    letter-spacing: 0.5px;
    background: linear-gradient(180deg, var(--silver-light) 0%, var(--silver-mid) 50%, var(--silver-light) 70%, var(--silver-dark) 100%);
    -webkit-background-clip: text;
    background-clip: text;
    color: transparent;
  }
  .tagline {
    top: 713px;
    font-size: 28px;
    font-weight: 400;
    letter-spacing: 1px;
    color: var(--muted);
  }

  .date {
    top: 832px;
    font-family: "Barlow Condensed", sans-serif;
    font-weight: 400;
    font-size: 31px;
    line-height: 41px;
    color: var(--white);
  }
  .access {
    top: 915px;
    font-size: 20px;
    font-weight: 600;
    letter-spacing: 6px;
    padding-left: 6px;
    color: var(--white);
  }

  .location-note {
    top: 997px;
    font-size: 16px;
    font-weight: 400;
    letter-spacing: 0.5px;
    color: var(--muted);
  }
  .host {
    top: 1042px;
    display: flex;
    justify-content: center;
    align-items: center;
    gap: 12px;
  }
  .host-dot {
    width: 26px;
    height: 26px;
    border-radius: 50%;
    background: var(--silver-mid);
  }
  .host-name {
    font-size: 22px;
    font-weight: 400;
    letter-spacing: 4px;
    color: var(--white);
  }
</style>
</head>
<body>
  <main class="flyer">
    <div class="band band--top"></div>
    <div class="rule rule--top-a"></div>
    <div class="rule rule--top-b"></div>
    <p class="row presenter"><strong>VELVETROLL</strong> Atlanta Presents</p>

    <div class="venue-mark" aria-hidden="true"></div>
    <p class="row venue-name">LANTERN</p>
    <p class="row venue-type">NIGHTCLUB</p>

    <div class="band band--middle"></div>
    <div class="rule rule--mid-a"></div>
    <div class="rule rule--mid-b"></div>
    <h1 class="headline">A POPUP<br>NIGHTCLUB<br>EXPERIENCE</h1>
    <p class="row tagline">For one night only</p>

    <p class="row date">FRIDAY, OCTOBER 18, 2013<br>PARTY BEGINS AT 9PM</p>
    <p class="row access">INVITE ONLY</p>

    <div class="band band--bottom"></div>
    <div class="rule rule--bot-a"></div>
    <div class="rule rule--bot-b"></div>
    <p class="row location-note">See invitation for location details</p>
    <div class="row host">
      <span class="host-dot" aria-hidden="true"></span>
      <span class="host-name">VELVETROLL ATLANTA</span>
    </div>
  </main>
</body>
</html>
```